Webdesign für Kleingruppenreisen in die Südsteiermark
Zielgruppe
Wir sind ein Start-Up Unternehmen, das als Kleingruppenreisen in die Südsteiermark veranstaltet; der Schwerpunkt liegt auf dem Kulinarischen. Zielgruppe sind Geschäftsleute, die diese Kurzreisen (Do-So) für Marketingzwecke oder als Mitarbeiterbonus (oder auch privat) nutzen möchten.
Aufgabenstellung
Die Homepage soll eine Online-Shop Möglichkeit bieten, in der die Reise (bisher gibt es nur einen Ablauf) gebucht werden kann. Optisch sollte sie sich an das bereits von Ihnen erstellte Logo anlehnen und möglichst ansprechende Fotos von der Südsteiermark, Graz, Leoben usw. enthalten. (Siehe die beiden Flyer und das Logo)
Wir haben inzwischen Bildfreigaben von Haldauer und dem Tourismusverband Kellwinden erhalten und können auch eigene Bilder zur Verfügung stellen. Bitte kontaktieren Sie uns dafür, wenn nötig.

```html
<!DOCTYPE html>
<html lang="de">
<head>
<meta charset="utf-8">
<title>GenussPfade – Reisen für Feinschmecker in die Steiermark</title>
<link href="https://fonts.googleapis.com/css2?family=Lato:wght@400;700&family=Montserrat:wght@400;600;700&display=swap" rel="stylesheet">
<style>
  :root {
    --cream: #fdf3ea;
    --white: #ffffff;
    --yellow: #f9c318;
    --yellow-dark: #f0b400;
    --red: #c8202f;
    --text: #3a3a3a;
    --muted: #8a8a8a;
    --border: #c9c2bb;
    --navy: #1b2d6b;
  }
  * { box-sizing: border-box; margin: 0; padding: 0; }
  html, body { width: 1182px; height: 1200px; overflow: hidden; }
  body { position: relative; background: var(--white); font-family: "Lato", sans-serif; color: var(--text); }
  .abs { position: absolute; }

  .site-header { left: 0; top: 0; width: 1182px; height: 186px; background: var(--cream); }
  .main-nav a { position: absolute; top: 149px; font-size: 14px; color: var(--text); text-decoration: none; }
  .brand { left: 441px; top: 85px; width: 300px; text-align: center; }
  .brand-name { font-size: 40px; font-weight: 700; color: var(--red); line-height: 1; }
  .brand-tagline { font-size: 12px; color: var(--text); margin-top: 6px; }
  .brand-dot { display: inline-block; width: 14px; height: 14px; border-radius: 50%; background: var(--yellow); margin-right: 8px; vertical-align: middle; }

  .hero { left: 0; top: 196px; width: 1182px; height: 184px;
    background: linear-gradient(100deg, #b98f6a 0%, #d8bc98 25%, #a8744f 45%, #e2c9a6 65%, #9c6a48 85%, #c9a47c 100%); }
  .divider { left: 0; width: 1182px; height: 6px; background: linear-gradient(#8f8b88, #d9d6d3 70%, transparent); }

  .tool-btn { top: 410px; height: 33px; border: 1px solid var(--border); border-radius: 2px; background: var(--white);
    font-family: "Montserrat", sans-serif; font-weight: 600; font-size: 12px; display: flex; align-items: center; }

  .sidebar-box { left: 162px; top: 456px; width: 221px; height: 95px; background: var(--cream); border: 1px solid var(--border); padding: 22px 29px; }
  .sidebar-title { color: var(--yellow); font-size: 15px; }
  .sidebar-sub { font-size: 13px; margin-top: 6px; }
  .pay-box { left: 162px; top: 565px; width: 221px; height: 45px; border: 1px solid var(--border); display: flex; align-items: center; justify-content: center;
    font-size: 20px; font-weight: 700; color: var(--navy); }
  .pay-box span.sq { width: 14px; height: 14px; background: var(--navy); margin-right: 8px; display: inline-block; }

  .filter-bar { left: 394px; top: 456px; width: 631px; height: 48px; background: var(--cream); border: 1px solid var(--border); }
  .select { position: absolute; top: 7px; height: 32px; background: var(--white); border: 1px solid var(--border); border-radius: 2px;
    font-family: "Montserrat", sans-serif; font-weight: 600; font-size: 12px; display: flex; align-items: center; }

  .product-card { left: 394px; top: 517px; width: 310px; height: 344px; border: 1px solid var(--border); border-radius: 4px; text-align: center; font-family: "Montserrat", sans-serif; }
  .product-photo { position: absolute; left: 42px; top: 12px; width: 229px; height: 229px;
    background: linear-gradient(180deg, #6f9a4a 0%, #8bb15a 35%, #7b6a55 60%, #4d3b2c 100%); }
  .product-title { position: absolute; top: 250px; width: 100%; font-weight: 600; font-size: 16px; line-height: 19px; }
  .product-price { position: absolute; top: 294px; width: 100%; font-weight: 700; font-size: 17px; }
  .product-links { position: absolute; top: 321px; width: 100%; color: var(--yellow); font-size: 12.5px; }
  .product-links span { margin: 0 8px; }

  .site-footer { left: 0; top: 947px; width: 1182px; height: 253px; background: var(--cream); }
  .newsletter { left: 162px; top: 964px; width: 859px; height: 51px; background: var(--yellow); border-radius: 5px; }
  .newsletter-input { position: absolute; left: 8px; top: 7px; width: 229px; height: 37px; background: var(--white); border: 1px solid #d8cfa5; border-radius: 2px; display: flex; align-items: center; }
  .newsletter-input .icon { width: 50px; height: 100%; border-right: 1px solid #d8cfa5; display: flex; align-items: center; justify-content: center; }
  .newsletter-input .placeholder { padding-left: 22px; font-size: 11px; color: var(--muted); }
  .newsletter-title { position: absolute; left: 283px; top: 9px; color: var(--white); font-size: 18px; font-weight: 700; }
  .newsletter-text { position: absolute; left: 283px; top: 32px; color: var(--white); font-size: 11px; }

  .footer-col { top: 1035px; font-size: 13.5px; line-height: 21.4px; }
  .footer-col h3 { color: var(--red); font-size: 14px; font-weight: 400; margin-bottom: 4px; }
  .footer-col.service, .footer-col.info { font-family: "Montserrat", sans-serif; font-size: 13px; }
  .footer-col.service h3, .footer-col.info h3 { font-family: "Lato", sans-serif; }
  .footer-brand { left: 800px; top: 1090px; width: 220px; text-align: center; }
  .footer-brand .brand-name { font-size: 28px; }
  .footer-brand .brand-tagline { font-size: 10px; }
</style>
</head>
<body>
  <header class="abs site-header">
    <nav class="main-nav">
      <a style="left:236px">Start</a>
      <a style="left:325px">Reise buchen</a>
      <a style="left:799px">Kontakt</a>
      <a style="left:908px">Impressum</a>
    </nav>
    <div class="abs brand">
      <div class="brand-name"><span class="brand-dot"></span>GenussPfade</div>
      <div class="brand-tagline">Reisen für Feinschmecker in die Steiermark</div>
    </div>
  </header>

  <div class="abs hero" role="img" aria-label="Nahaufnahme vieler gebrauchter Weinkorken"></div>
  <div class="abs divider" style="top:386px"></div>

  <div class="abs tool-btn" style="left:717px;width:33px;justify-content:center">
    <svg width="22" height="20" viewBox="0 0 24 22"><path d="M12 21 2 11a6 6 0 0 1 10-7 6 6 0 0 1 10 7z" fill="var(--yellow)"/></svg>
  </div>
  <div class="abs tool-btn" style="left:760px;width:134px;padding-left:6px">
    <svg width="26" height="26" viewBox="0 0 26 26"><circle cx="13" cy="8" r="6" fill="var(--yellow)"/><path d="M1 26c0-8 5-11 12-11s12 3 12 11z" fill="var(--yellow)"/></svg>
    <span style="margin-left:12px">Mein Konto</span>
  </div>
  <div class="abs tool-btn" style="left:904px;width:121px;padding:0 10px;justify-content:space-between">
    <svg width="28" height="24" viewBox="0 0 28 24"><path d="M1 2h5l3 13h14l3-10H8" fill="none" stroke="var(--yellow)" stroke-width="3"/><path d="M8 6h17l-3 8H10z" fill="var(--yellow)"/><circle cx="11" cy="20" r="2.5" fill="var(--yellow)"/><circle cx="21" cy="20" r="2.5" fill="var(--yellow)"/></svg>
    <span>0,00 €</span>
  </div>

  <aside>
    <div class="abs sidebar-box">
      <div class="sidebar-title">GenussPfade</div>
      <div class="sidebar-sub">Reisen 2018</div>
    </div>
    <div class="abs pay-box"><span class="sq"></span>PayNest</div>
  </aside>

  <div class="abs filter-bar">
    <div class="select" style="left:9px;width:148px;padding:0 12px">
      <svg width="10" height="11" viewBox="0 0 10 11"><path d="M0 0h10L6 5v6L4 9V5z" fill="var(--yellow)"/></svg>
      <span style="margin-left:6px">Filtern</span>
      <svg style="margin-left:auto" width="13" height="8" viewBox="0 0 13 8"><path d="M1 1l5.5 5.5L12 1" fill="none" stroke="var(--yellow)" stroke-width="2"/></svg>
    </div>
    <div class="select" style="left:395px;width:198px">
      <span style="padding-left:14px;flex:1">Erscheinungdatum</span>
      <span style="width:32px;height:100%;border-left:1px solid var(--border);display:flex;align-items:center;justify-content:center">
        <svg width="13" height="8" viewBox="0 0 13 8"><path d="M1 1l5.5 5.5L12 1" fill="none" stroke="var(--yellow)" stroke-width="2"/></svg>
      </span>
    </div>
  </div>

  <article class="abs product-card">
    <div class="product-photo" role="img" aria-label="Weinglas auf Holztisch im Weingarten mit Trauben, Nüssen und Blumen"></div>
    <div class="product-title">GenussPfad-Reise<br>Südsteiermark</div>
    <div class="product-price">ab 1.650 €*</div>
    <div class="product-links"><span>⇆ vergleichen</span><span>♥ merken</span></div>
  </article>

  <div class="abs divider" style="top:941px"></div>
  <footer class="abs site-footer"></footer>

  <div class="abs newsletter">
    <div class="newsletter-input">
      <span class="icon"><svg width="26" height="18" viewBox="0 0 26 18"><rect x="1" y="1" width="24" height="16" fill="#fbe7a6" stroke="var(--yellow-dark)"/><path d="M1 1l12 9 12-9M1 17l9-8M25 17l-9-8" fill="none" stroke="var(--yellow-dark)"/></svg></span>
      <span class="placeholder">Ihre E-Mail Adresse</span>
    </div>
    <div class="newsletter-title">Newsletter</div>
    <div class="newsletter-text">Abonnieren Sie unseren kostenlosen Newsletter und verpasse keine Neuigkeiten</div>
  </div>

  <div class="abs footer-col" style="left:162px">
    <h3>Telefon</h3>
    XXXXXXXXXXX<br>Montag bis Freitag<br>von XX bis XX Uhr
  </div>
  <div class="abs footer-col service" style="left:376px">
    <h3>Service</h3>
    Kontakt<br>&nbsp;Zahlungsbedingungen<br>AGB<br>Widerrufsrecht<br>Widerrufsformular<br>Partnerprogramm
  </div>
  <div class="abs footer-col info" style="left:625px">
    <h3>Informationen</h3>
    Über uns<br>Datenschutz<br>Impressum<br>Newsletter
  </div>
  <div class="abs brand footer-brand">
    <div class="brand-name"><span class="brand-dot"></span>GenussPfade</div>
    <div class="brand-tagline">Reisen für Feinschmecker in die Steiermark</div>
  </div>
</body>
</html>
```